Packaging design for a reclosable bag for our product

We have a logo, and we need to put it on packaging for our product and while we want the look to be simple, we want it to follow good design principles and also contain spaces for other product descriptions.

There will be 5 sizes at launch so I'd like 5 variations, one for each size.

I've included a few mockups of the type of bag that I made but they are all just rough ideas that I had.

I want the brand to look scientific and methodical and even a bit quirky, as in "wow this is a serious product but also a bit unusual."

```html
<!DOCTYPE html>
<html lang="en">
<head>
<meta charset="utf-8">
<title>Kelvo Bias Lighting – Extra Large Pack</title>
<link rel="stylesheet" href="https://fonts.googleapis.com/css2?family=Open+Sans:wdth,wght@75..100,300..700&display=swap">
<style>
  :root {
    --pack-black: #000000;
    --band-grey: #4d4d4d;
    --ink-white: #ffffff;
  }
  html, body {
    margin: 0;
    padding: 0;
    overflow: hidden;
    background: var(--pack-black);
  }
  .pack {
    position: relative;
    width: 960px;
    height: 1200px;
    background: var(--pack-black);
    overflow: hidden;
    font-family: "Open Sans", Arial, sans-serif;
    color: var(--ink-white);
  }
  .pack__bands {
    position: absolute;
    inset: 0;
  }
  .pack__bands polygon { fill: var(--band-grey); }
  .pack__text {
    position: absolute;
    margin: 0;
    line-height: 1;
    white-space: nowrap;
  }
  .size-label {
    right: 197px;
    top: 333px;
    font-size: 47px;
    font-weight: 300;
    font-stretch: 75%;
  }
  .size-length {
    right: 197px;
    top: 377px;
    font-size: 72px;
    font-weight: 500;
    font-stretch: 87.5%;
  }
  .brand-name {
    position: absolute;
    left: 198px;
    top: 460px;
    width: 564px;
    height: 279px;
    display: flex;
    align-items: center;
    justify-content: center;
    margin: 0;
    font-size: 230px;
    font-weight: 700;
    font-stretch: 75%;
    line-height: 1;
    color: var(--ink-white);
  }
  .product-name {
    left: 195px;
    top: 750px;
    font-size: 80px;
    font-weight: 500;
    font-stretch: 87.5%;
  }
  .spec {
    left: 199px;
    font-size: 46px;
    font-weight: 300;
    font-stretch: 75%;
  }
  .spec--primary { top: 880px; }
  .spec--secondary { top: 958px; }
</style>
</head>
<body>
  <main class="pack">
    <svg class="pack__bands" width="960" height="1200" viewBox="0 0 960 1200" aria-hidden="true">
      <polygon class="band band--top-wedge" points="0,84 300,441 0,441"/>
      <polygon class="band band--top-stripe" points="0,0 39,0 409,441 324,441 0,55"/>
      <polygon class="band band--bottom-stripe" points="591,758 675,758 960,1099 960,1200"/>
      <polygon class="band band--bottom-wedge" points="700,758 960,758 960,1068"/>
    </svg>

    <p class="pack__text size-label">Extra Large</p>
    <p class="pack__text size-length">5 meters</p>

    <h1 class="brand-name">Kelvo</h1>

    <h2 class="pack__text product-name">Bias Lighting</h2>

    <p class="pack__text spec spec--primary">Simulated D65 CRI 90+</p>
    <p class="pack__text spec spec--secondary">6500K White Bias Lighting</p>
  </main>
</body>
</html>
```